Modernize and improve usability of our webpage www.lernwandel.ch (4 languages, mostly static content)

Need to modernize and freshen up the webpages of our association: www.lernwandel.ch We offer apprenticeship exchanges within Switzerland and abroad. Young people can inform and enroll online. We do the matchmaking with work locations and organize logistics, stay overs etc.
The webpage needs to be in 4 languages (German, French, Italian and English). The main pages will be:
- Landing page: what we do, targeted to our apprentices / young people who enroll for the stages.
- Sup-Page: Registration form for interested apprentices to sign up for the program
- Sub-Page "Company", the firms who would like to send their apprentices on a internship and info on how to join the program
- Sub-Page "Host Family", private people who would be interested in hosting the apprentices (for free) during the stages. Find out about the reqiurements for the host families
- Sub-Page "About Us", who we are, executive team, board of director, our sponsor "Falkner Circle Switzerland"
- Footer: contact (E-Mail, Telephone, WhatsApp), Bank details (IBAN Number), Partnerlogo of Falkner-Circle (see uploaded jpg), Social-Media Links (Facebook, LinkedIn)

Target Market(s)

Young people looking for a "apprenticeship" stage within Switzerland or going from Switzerland abroad

Industry/Entity Type

Apprenticeships: cooks, builders, craftsman, office support, etc.

Number of Pages Required

5+ page

Font styles to use
Other font styles liked:
• Lato (sans serif)

Requirements
Must have
• use colors shown on uploaded PDF-Slides: Make the BLUE the MAIN color, the ORANGE as a secondary color
Nice to have
• Forms using e.g. google forms or survey-monkey forms (external links, no code). Matching & appealing visuals showing young apprentices (can use stock photos)

```html
<!DOCTYPE html>
<html lang="en">
<head>
<meta charset="utf-8">
<title>Lernwandel – Apprenticeship Exchange</title>
<link href="https://fonts.googleapis.com/css2?family=Open+Sans:wght@400;600;700;800&display=swap" rel="stylesheet">
<style>
:root{
  --navy:#1c2b4f;
  --navy-dark:#14203d;
  --navy-soft:#2a3a62;
  --orange:#f15a22;
  --grey:#f2f3f5;
  --line:#e2e4e9;
  --text:#5d6473;
  --white:#ffffff;
}
*{box-sizing:border-box;margin:0;padding:0}
html,body{width:1200px;height:5300px;overflow:hidden}
body{font-family:"Open Sans",sans-serif;color:var(--text);background:var(--white);position:relative;font-size:14px;line-height:1.6}
section,header,footer,nav,div{position:relative}
.abs{position:absolute}
h1,h2,h3,h4{color:var(--navy);font-weight:700;line-height:1.2}
.eyebrow{font-size:11px;font-weight:700;letter-spacing:1px;text-transform:uppercase;color:var(--text)}
.btn{display:inline-flex;align-items:center;gap:10px;background:var(--orange);color:var(--white);font-weight:600;font-size:14px;padding:11px 22px;border-radius:2px}
.btn svg{width:16px;height:16px}
.photo{background:linear-gradient(135deg,#8a7a6a,#c9b79f 50%,#6d7c8e)}

/* top strip */
.topbar{height:40px;background:var(--navy-dark);color:#aab3c6;font-size:12px;display:flex;align-items:center;justify-content:space-between;padding:0 72px}
.topbar span{margin-right:24px}

/* header */
.site-header{height:130px;display:flex;align-items:center;justify-content:space-between;padding:0 72px}
.brand{font-size:40px;font-weight:800;color:var(--orange);letter-spacing:-1px}
.contact-blocks{display:flex;gap:56px}
.contact-block{display:flex;gap:12px;align-items:flex-start}
.contact-block svg{width:26px;height:26px;color:var(--orange)}
.contact-block b{display:block;color:var(--navy);font-size:14px}
.contact-block small{font-size:12px;color:var(--text)}

/* nav */
.main-nav{margin:0 72px;height:44px;background:var(--navy);display:flex;align-items:stretch;z-index:2}
.main-nav a{color:var(--white);font-size:12px;font-weight:700;text-transform:uppercase;display:flex;align-items:center;padding:0 28px;text-decoration:none}
.main-nav a.active{background:var(--orange)}
.main-nav a.quote{margin-left:auto}

/* hero */
.hero{height:618px;margin-top:-2px;background:linear-gradient(180deg,#3a4258 0%,#2b3247 50%,#3b3f4e 100%);text-align:center;color:var(--white)}
.hero h1{color:var(--white);font-size:44px;font-weight:700;padding-top:140px;line-height:1.25}
.hero p{font-size:15px;margin:18px auto 26px;width:380px;color:#dfe3ec;line-height:1.5}
.btn-outline{display:inline-block;border:2px solid var(--white);color:var(--white);font-size:12px;font-weight:700;padding:12px 22px;text-transform:uppercase}

/* features */
.features{height:520px;background:var(--grey);text-align:center}
.features .eyebrow{padding-top:56px}
.features h2{font-size:34px;margin-top:10px}
.feature-cards{position:absolute;top:194px;left:64px;right:72px;display:flex;gap:44px}
.feature-card{flex:1;height:240px;background:var(--white);border:1px solid var(--line);padding-top:58px}
.feature-card .num{position:absolute;top:18px;right:22px;font-size:16px;color:var(--text)}
.icon-ring{width:64px;height:64px;border-radius:50%;background:#fde8de;margin:0 auto;display:flex;align-items:center;justify-content:center;color:var(--orange)}
.icon-ring svg{width:30px;height:30px}
.feature-card h3{font-size:18px;margin-top:22px}
.feature-card a{display:block;margin-top:8px;font-size:11px;font-weight:700;color:var(--orange);text-transform:uppercase}

/* about */
.about{height:598px}
.about-text{position:absolute;left:92px;top:64px;width:500px}
.about-text h2{font-size:34px;margin-top:10px}
.about-text h3{font-size:22px;margin-top:26px}
.about-text p{margin-top:16px;font-size:14px}
.perks{display:flex;gap:60px;margin-top:28px}
.perk{display:flex;gap:12px;align-items:center;color:var(--navy);font-weight:600;font-size:16px;line-height:1.3}
.perk svg{width:40px;height:40px;color:var(--orange)}
.about .btn{margin-top:32px}
.about-photo{position:absolute;left:680px;top:78px;width:420px;height:420px;border-radius:50%;border:3px solid var(--navy)}
.about-photo .photo{position:absolute;inset:14px;border-radius:50%;background:linear-gradient(135deg,#d9d2c8,#b59d83 55%,#7c6d60)}
.badge{position:absolute;left:952px;top:386px;width:160px;height:160px;border-radius:50%;background:var(--navy);border:8px solid var(--white)}

/* audience tabs */
.tabs{height:100px;margin:0 64px 0 64px;display:flex;align-items:stretch;border:1px solid var(--line)}
.tab{flex:1;display:flex;align-items:center;justify-content:center;color:var(--navy);font-weight:600;font-size:15px;border-left:1px solid var(--line)}
.tab:first-child{border-left:0;background:var(--orange);color:var(--white)}
.tab:first-child::after{content:"";position:absolute;bottom:-14px;left:50%;margin-left:-14px;border-left:14px solid transparent;border-right:14px solid transparent;border-top:14px solid var(--orange)}
.exchange{height:532px;background:linear-gradient(180deg,var(--navy-soft),var(--navy));color:#d2d8e6}
.exchange-photo{position:absolute;left:152px;top:112px;width:432px;height:320px;background:linear-gradient(135deg,#a99580,#d7c6ad 50%,#6e7f95)}
.exchange-text{position:absolute;left:620px;top:92px;width:470px}
.exchange-text .eyebrow{color:var(--orange)}
.exchange-text h2{color:var(--white);font-size:34px;margin-top:12px}
.exchange-text h3{color:var(--white);font-size:18px;font-weight:600;margin-top:24px}
.exchange-text p{font-size:13.5px;margin-top:14px;color:#d2d8e6}
.exchange-text .btn{margin-top:24px}

/* gallery */
.gallery{height:708px;text-align:center}
.gallery .eyebrow{padding-top:60px}
.gallery h2{font-size:34px;margin-top:10px}
.tile{position:absolute}
.t1{left:88px;top:168px;width:252px;height:232px;background:linear-gradient(135deg,#7f6a58,#c4a98c)}
.t2{left:352px;top:168px;width:240px;height:232px;background:linear-gradient(135deg,#8c9bb0,#d2c3b0)}
.t3{left:612px;top:168px;width:496px;height:232px;background:linear-gradient(135deg,#5e6670,#a5a9ae 60%,#c6b59c)}
.t4{left:88px;top:420px;width:504px;height:232px;background:linear-gradient(135deg,#c7a27a,#8c7a6b 55%,#5d6a7c)}
.t5{left:612px;top:420px;width:248px;height:232px;background:linear-gradient(135deg,#b8b0a2,#6d7f92)}
.t6{left:872px;top:420px;width:236px;height:232px;background:linear-gradient(135deg,#a27d5f,#dcc4a2)}

/* steps */
.steps{height:702px;display:flex}
.steps-left{width:600px;background:var(--navy);color:#d2d8e6;padding:104px 72px 0 96px}
.steps-left .eyebrow{color:#d2d8e6}
.steps-left h2{color:var(--white);font-size:34px;margin-top:12px}
.steps-left h3{color:var(--white);font-size:18px;font-weight:600;margin-top:44px}
.steps-left p{font-size:13.5px;margin-top:16px}
.steps-left .btn{margin-top:34px}
.steps-right{width:600px;background:var(--grey)}
.step-line{position:absolute;left:12px;top:120px;width:2px;height:480px;background:var(--line)}
.step{position:absolute;left:-42px;display:flex;gap:40px;align-items:flex-start}
.step-box{width:100px;height:100px;background:var(--white);box-shadow:0 6px 18px rgba(28,43,79,.12);display:flex;align-items:center;justify-content:center;color:var(--orange);flex:none}
.step-box svg{width:42px;height:42px}
.step-no{position:absolute;top:-12px;right:-12px;width:28px;height:28px;border-radius:50%;background:var(--orange);color:var(--white);font-size:11px;font-weight:700;display:flex;align-items:center;justify-content:center}
.step h4{font-size:16px;padding-top:4px}
.step p{font-size:12.5px;width:380px;margin-top:8px}

/* enroll */
.enroll{height:660px}
.enroll-text{position:absolute;left:132px;top:160px;width:400px}
.enroll-text h2{font-size:40px;font-weight:700}
.enroll-text .sub{font-size:32px;color:var(--orange);font-weight:400;line-height:1.2}
.enroll-text p{font-size:13px;margin-top:22px}
.enroll-contacts{list-style:none;margin-top:40px}
.enroll-contacts li{display:flex;gap:18px;align-items:center;margin-bottom:26px;font-size:14px;color:var(--text)}
.enroll-contacts svg{width:20px;height:20px;color:var(--orange)}
.form-card{position:absolute;left:588px;top:72px;width:492px;height:528px;background:var(--white);border-top:4px solid var(--navy);box-shadow:0 6px 24px rgba(28,43,79,.12);padding:34px 36px}
.form-card label{display:block;color:var(--navy);font-weight:700;font-size:13px}
.field{height:42px;border:1px solid var(--line);margin:8px 0 24px;padding:0 14px;display:flex;align-items:center;font-size:12px;color:#a8adb8}
.form-row{display:flex;gap:20px}
.form-row > div{flex:1}
.field.area{height:130px;align-items:flex-start;padding-top:10px}
.submit{display:inline-block;background:var(--orange);color:var(--white);font-weight:700;font-size:12px;padding:12px 30px;text-transform:uppercase}

/* footer */
.site-footer{height:600px;background:var(--navy-dark);color:#b9c1d2}
.foot-col{position:absolute;top:76px}
.foot-brand .brand{font-size:38px}
.foot-brand b{display:block;color:var(--white);font-size:20px;margin-top:26px}
.foot-brand small{display:block;color:var(--white);font-size:14px;font-weight:600}
.foot-brand p{font-size:13px;width:300px;margin-top:14px}
.foot-brand .more{display:flex;gap:8px;align-items:center;color:var(--white);font-weight:700;margin-top:18px}
.foot-col h4{color:var(--white);font-size:22px;font-weight:600}
.links{display:flex;gap:40px;margin-top:26px}
.links ul{list-style:none}
.links li{font-size:13px;margin-bottom:10px;display:flex;gap:10px;align-items:center}
.links li::before{content:"";width:6px;height:6px;border-top:2px solid var(--white);border-right:2px solid var(--white);transform:rotate(45deg)}
.news p{font-size:13px;width:280px;margin-top:26px}
.news-field{width:300px;height:44px;background:var(--white);margin-top:20px;display:flex;align-items:center;justify-content:space-between;padding-left:16px;font-size:12px;color:#8a90a0}
.news-field span.go{width:48px;height:44px;background:var(--orange);display:flex;align-items:center;justify-content:center;color:var(--white)}
.info-bar{position:absolute;left:88px;right:88px;top:440px;height:84px;background:var(--navy-soft);display:flex;align-items:center;justify-content:space-around}
.info{display:flex;gap:16px;align-items:center}
.info svg{width:28px;height:28px;color:var(--orange)}
.info b{display:block;color:var(--white);font-size:14px}
.info span{font-size:13px;color:#d2d8e6}
.copyright{position:absolute;left:88px;right:88px;top:548px;display:flex;justify-content:space-between;font-size:12px}
.copyright nav span{margin-left:28px}
.to-top{position:absolute;right:32px;top:552px;width:36px;height:36px;background:var(--orange);display:flex;align-items:center;justify-content:center;color:var(--white)}
</style>
</head>
<body>

<div class="topbar">
  <div><span>800-555-0142</span><span>info@lernwandel.ch</span></div>
  <div>Apprenticeship exchange Switzerland</div>
</div>

<header class="site-header">
  <div class="brand">lernwandel</div>
  <div class="contact-blocks">
    <div class="contact-block">
      <svg viewBox="0 0 24 24" fill="none" stroke="currentColor" stroke-width="1.8"><rect x="3" y="5" width="18" height="14" rx="1"/><path d="M3 6l9 7 9-7"/></svg>
      <div><b>Email</b><small>info@lernwandel.ch</small></div>
    </div>
    <div class="contact-block">
      <svg viewBox="0 0 24 24" fill="none" stroke="currentColor" stroke-width="1.8"><path d="M5 3h4l2 5-3 2a11 11 0 005 5l2-3 5 2v4a2 2 0 01-2 2A17 17 0 013 5a2 2 0 012-2z"/></svg>
      <div><b>Call Now</b><small>800-555-0142</small></div>
    </div>
    <div class="contact-block">
      <svg viewBox="0 0 24 24" fill="none" stroke="currentColor" stroke-width="1.8"><path d="M12 22s7-7 7-12a7 7 0 00-14 0c0 5 7 12 7 12z"/><circle cx="12" cy="10" r="2.5"/></svg>
      <div><b>Find Us</b><small>12 Lindenweg, Bern</small></div>
    </div>
  </div>
</header>

<nav class="main-nav">
  <a class="active">Home</a><a>About Us</a><a>Services</a><a>Testimonials</a><a>Blog</a><a>Contact Us</a><a class="quote">Request a Quote</a>
</nav>

<section class="hero" role="img" aria-label="Group of young apprentices working together, darkened behind the headline">
  <h1>Unlocking Potential,<br>Exchanging Possibilities</h1>
  <p>Lorem ipsum dolor sit amet, consectetur adipiscing elit, sed do eiusmod tempor incidid</p>
  <span class="btn-outline">Call Us Today</span>
</section>

<section class="features">
  <div class="eyebrow">Why we're the best</div>
  <h2>Simplicity &amp; Efficiency</h2>
  <div class="feature-cards">
    <div class="feature-card"><span class="num">01</span>
      <div class="icon-ring"><svg viewBox="0 0 24 24" fill="none" stroke="currentColor" stroke-width="1.6"><circle cx="12" cy="12" r="9"/><path d="M3 12h18M12 3c3 3 3 15 0 18M12 3c-3 3-3 15 0 18"/></svg></div>
      <h3>Global Perspective</h3><a>Read more</a></div>
    <div class="feature-card"><span class="num">02</span>
      <div class="icon-ring"><svg viewBox="0 0 24 24" fill="none" stroke="currentColor" stroke-width="1.6"><path d="M4 14v-2a8 8 0 0116 0v2"/><rect x="3" y="13" width="4" height="6" rx="1"/><rect x="17" y="13" width="4" height="6" rx="1"/></svg></div>
      <h3>Support System</h3><a>Read more</a></div>
    <div class="feature-card"><span class="num">03</span>
      <div class="icon-ring"><svg viewBox="0 0 24 24" fill="none" stroke="currentColor" stroke-width="1.6"><path d="M9 18h6M10 21h4M12 3a6 6 0 00-4 10.5c.8.8 1 1.5 1 2.5h6c0-1 .2-1.7 1-2.5A6 6 0 0012 3z"/></svg></div>
      <h3>Skill Development</h3><a>Read more</a></div>
  </div>
</section>

<section class="about">
  <div class="about-text">
    <div class="eyebrow">About our company</div>
    <h2>Elevate, Exchange, Excel</h2>
    <h3>Crafting Careers, Connecting Capabilities</h3>
    <p>Lorem ipsum dolor sit amet, consectetur adipiscing elit, sed do eiusmod tempor incididunt ut labore et dolore magna aliqua. Ut enim ad minim veniam, quis nostrud exercitation ullamco laboris nisi ut aliquip ex ea commodo consequat. Duis aute irure dolor in reprehenderit in voluptate velit esse cillum dolore eu fugiat nulla pariatur. Excepteur sint occaecat cupidatat non proident, sunt in culpa qui officia deserunt mollit.</p>
    <div class="perks">
      <div class="perk"><svg viewBox="0 0 24 24" fill="none" stroke="currentColor" stroke-width="1.4"><path d="M12 2l2.9 6.3 6.9.7-5.2 4.6 1.5 6.8L12 17l-6.1 3.4 1.5-6.8L2.2 9l6.9-.7z"/></svg><span>Industry<br>Partnerships</span></div>
      <div class="perk"><svg viewBox="0 0 24 24" fill="none" stroke="currentColor" stroke-width="1.4"><path d="M3 20l9-16 9 16z"/><path d="M8 20l4-7 4 7"/></svg><span>Supportive<br>Community</span></div>
    </div>
    <span class="btn">Contact us <svg viewBox="0 0 16 16" fill="none" stroke="currentColor" stroke-width="2"><path d="M2 8h11M9 4l4 4-4 4"/></svg></span>
  </div>
  <div class="about-photo"><div class="photo" role="img" aria-label="Smiling young office apprentice on the telephone"></div></div>
  <div class="badge"></div>
</section>

<div class="tabs">
  <div class="tab">For Apprentices</div>
  <div class="tab">For Host Families</div>
  <div class="tab">For Companies</div>
</div>

<section class="exchange">
  <div class="exchange-photo" role="img" aria-label="Apprentices gathered around a table in a workshop session"></div>
  <div class="exchange-text">
    <div class="eyebrow">About our company</div>
    <h2>Exchanging Skills</h2>
    <h3>Igniting Careers, Exchanging Expertise</h3>
    <p>Lorem ipsum dolor sit amet, consectetur adipiscing elit, sed do eiusmod tempor incididunt ut labore et dolore magna aliqua. Ut enim ad minim veniam, quis nostrud exercitation ullamco laboris nisi ut aliquip ex ea commodo consequat. Duis aute irure dolor in reprehenderit in voluptate velit esse cillum dolore eu fugiat nulla pariatur. Excepteur sint occaecat cupidatat non proident, sunt in culpa qui officia deserunt mollit anim.</p>
    <span class="btn">Contact us <svg viewBox="0 0 16 16" fill="none" stroke="currentColor" stroke-width="2"><path d="M2 8h11M9 4l4 4-4 4"/></svg></span>
  </div>
</section>

<section class="gallery">
  <div class="eyebrow">Our gallery</div>
  <h2>Our Recent Projects</h2>
  <div class="tile t1" role="img" aria-label="Young apprentices smiling in a group"></div>
  <div class="tile t2" role="img" aria-label="Apprentices working at laptops"></div>
  <div class="tile t3" role="img" aria-label="Two apprentices laughing in front of a café sign"></div>
  <div class="tile t4" role="img" aria-label="Team of apprentices at a desk with a laptop"></div>
  <div class="tile t5" role="img" aria-label="Apprentices walking through a workshop hall"></div>
  <div class="tile t6" role="img" aria-label="Apprentice preparing food in a kitchen"></div>
</section>

<section class="steps">
  <div class="steps-left">
    <div class="eyebrow">How to join</div>
    <h2>Steps to Enroll</h2>
    <h3>Your Path to Success: Learn, Thrive</h3>
    <p>Lorem ipsum dolor sit amet, consectetur adipiscing elit, sed do eiusmod tempor incididunt ut labore et dolore magna aliqua. Ut enim ad minim veniam, quis nostrud exercitation ullamco laboris nisi ut aliquip ex ea commodo consequat. Duis aute irure dolor in reprehenderit in voluptate velit esse cillum dolore.</p>
    <span class="btn">Contact us <svg viewBox="0 0 16 16" fill="none" stroke="currentColor" stroke-width="2"><path d="M2 8h11M9 4l4 4-4 4"/></svg></span>
  </div>
  <div class="steps-right">
    <div class="step-line"></div>
    <div class="step" style="top:100px">
      <div class="step-box"><span class="step-no">01</span><svg viewBox="0 0 24 24" fill="none" stroke="currentColor" stroke-width="1.6"><rect x="3" y="5" width="18" height="14" rx="1"/><path d="M3 6l9 7 9-7"/></svg></div>
      <div><h4>Enroll for<br>the program</h4><p>Lorem ipsum dolor sit amet, consectetur adipiscing elit sed do eiusmod tempor incididunt ut labore et dolore magna aliqua.</p></div>
    </div>
    <div class="step" style="top:330px">
      <div class="step-box"><span class="step-no">02</span><svg viewBox="0 0 24 24" fill="none" stroke="currentColor" stroke-width="1.6"><path d="M4 5h16v10H9l-5 4z"/><path d="M8 9h8M8 12h5"/></svg></div>
      <div><h4>Consult<br>Our Expert Team</h4><p>Lorem ipsum dolor sit amet, consectetur adipiscing elit sed do eiusmod tempor incididunt ut labore et dolore magna aliqua.</p></div>
    </div>
    <div class="step" style="top:560px">
      <div class="step-box"><span class="step-no">03</span><svg viewBox="0 0 24 24" fill="none" stroke="currentColor" stroke-width="1.6"><circle cx="8" cy="8" r="3"/><circle cx="16" cy="8" r="3"/><path d="M2 20c0-3.5 2.7-6 6-6s6 2.5 6 6M12 20c0-3.5 1.7-6 4-6 3.3 0 6 2.5 6 6"/></svg></div>
      <div><h4>Get<br>Apprenticeship</h4><p>Lorem ipsum dolor sit amet, consectetur adipiscing elit sed do eiusmod tempor incididunt ut labore et dolore magna aliqua.</p></div>
    </div>
  </div>
</section>

<section class="enroll">
  <div class="enroll-text">
    <h2>Enroll</h2>
    <div class="sub">for program</div>
    <p>Lorem ipsum dolor sit amet, consectetur adipiscing elit, sed do eiusmod tempor incididunt ut labore et dolore magna aliqua.</p>
    <ul class="enroll-contacts">
      <li><svg viewBox="0 0 24 24" fill="none" stroke="currentColor" stroke-width="1.8"><path d="M12 22s7-7 7-12a7 7 0 00-14 0c0 5 7 12 7 12z"/><circle cx="12" cy="10" r="2.5"/></svg>12 Lindenweg, Bern</li>
      <li><svg viewBox="0 0 24 24" fill="none" stroke="currentColor" stroke-width="1.8"><path d="M5 3h4l2 5-3 2a11 11 0 005 5l2-3 5 2v4a2 2 0 01-2 2A17 17 0 013 5a2 2 0 012-2z"/></svg>+41 31 555 01 42</li>
      <li><svg viewBox="0 0 24 24" fill="none" stroke="currentColor" stroke-width="1.8"><rect x="3" y="5" width="18" height="14" rx="1"/><path d="M3 6l9 7 9-7"/></svg>info@lernwandel.ch</li>
    </ul>
  </div>
  <form class="form-card">
    <label>Full Name:</label><div class="field">Your full name</div>
    <div class="form-row">
      <div><label>Email:</label><div class="field">Your email</div></div>
      <div><label>Phone no:</label><div class="field">Your phone</div></div>
    </div>
    <label>Messages:</label><div class="field area">Your message</div>
    <span class="submit">Submit</span>
  </form>
</section>

<footer class="site-footer">
  <div class="foot-col foot-brand" style="left:88px">
    <div class="brand">lernwandel</div>
    <b>800-555-0142</b>
    <small>Call for free consultation</small>
    <p>Lorem ipsum dolor sit amet, consectetur adipiscing elit, sed do eiusmod tempor incididunt ut labore et dolore magna aliqua.</p>
    <div class="more">Read more <svg width="14" height="14" viewBox="0 0 16 16" fill="none" stroke="currentColor" stroke-width="2"><path d="M2 8h11M9 4l4 4-4 4"/></svg></div>
  </div>
  <div class="foot-col" style="left:436px">
    <h4>Useful Links</h4>
    <div class="links">
      <ul><li>About Company</li><li>Leadership</li><li>Blog Post</li><li>FAQ's</li><li>Certification</li><li>Testimonials</li></ul>
      <ul><li>Services</li><li>Industries</li><li>Feedback</li><li>Partners</li><li>Pricing</li><li>Contact</li></ul>
    </div>
  </div>
  <div class="foot-col news" style="left:790px">
    <h4>Newsletter</h4>
    <p>Don't miss to subscribe to our news feeds, kindly fill the form below.</p>
    <div class="news-field">Your Email Address<span class="go"><svg width="16" height="16" viewBox="0 0 16 16" fill="none" stroke="currentColor" stroke-width="2"><path d="M2 8h11M9 4l4 4-4 4"/></svg></span></div>
  </div>
  <div class="info-bar">
    <div class="info"><svg viewBox="0 0 24 24" fill="none" stroke="currentColor" stroke-width="1.8"><path d="M12 22s7-7 7-12a7 7 0 00-14 0c0 5 7 12 7 12z"/><circle cx="12" cy="10" r="2.5"/></svg><div><b>Location</b><span>12 Lindenweg, Bern</span></div></div>
    <div class="info"><svg viewBox="0 0 24 24" fill="none" stroke="currentColor" stroke-width="1.8"><rect x="3" y="5" width="18" height="14" rx="1"/><path d="M3 6l9 7 9-7"/></svg><div><b>Mail us</b><span>team@lernwandel.ch</span></div></div>
    <div class="info"><svg viewBox="0 0 24 24" fill="none" stroke="currentColor" stroke-width="1.8"><circle cx="12" cy="12" r="9"/><path d="M12 7v5l3 2"/></svg><div><b>Office hrs</b><span>9:00am to 7:00pm (Mon-Sat)</span></div></div>
  </div>
  <div class="copyright">
    <span>© Lernwandel Apprentice Exchange</span>
    <nav><span>Privacy Policy</span><span>Terms &amp; Conditions</span><span>Site Map</span></nav>
  </div>
  <div class="to-top"><svg width="16" height="16" viewBox="0 0 16 16" fill="none" stroke="currentColor" stroke-width="2"><path d="M8 13V3M4 7l4-4 4 4"/></svg></div>
</footer>

</body>
</html>
```